TORV.
TORVALE ENTERTAINMENT & MEDIA
TORV. -
Creative Brief
Use specific fonts
any thing which suits with the LOGO provided
Professional
VIKRAM TULSE
MR.
D-47, WEST ENCLAVE-II , GURGAON 122001,HARYANA, INDIA
vikram@torv.co.in
www.torv.co.in
LOG IN THE CENTRE

```html
<!DOCTYPE html>
<html lang="en">
<head>
<meta charset="utf-8">
<title>TORV. Business Cards</title>
<link href="https://fonts.googleapis.com/css2?family=Source+Sans+3:wght@400;600;700&display=swap" rel="stylesheet">
<style>
  :root {
    --backdrop: #e9e6e1;
    --card: #ffffff;
    --brand-blue: #1d5f8f;
    --brand-blue-light: #3c93c6;
    --ink: #3e3e3e;
    --ink-soft: #6a6a6a;
    --rule: #c9c9c9;
  }
  * { box-sizing: border-box; margin: 0; padding: 0; }
  html, body {
    width: 1200px; height: 852px; overflow: hidden;
    background: var(--backdrop);
    font-family: "Source Sans 3", "Myriad Pro", Arial, sans-serif;
  }
  .stage { position: relative; width: 1200px; height: 852px; }

  .card {
    position: absolute;
    width: 620px; height: 360px;
    background: var(--card);
    border-radius: 16px;
    overflow: hidden;
    box-shadow: 0 10px 28px rgba(0,0,0,.18);
  }
  .card--front { left: 60px; top: 56px; }
  .card--back  { left: 520px; top: 436px; }

  .base-band {
    position: absolute; left: 0; right: 0; bottom: 0;
    height: 30px;
    background: var(--brand-blue);
  }
  .base-rule {
    position: absolute; left: 0; right: 0; bottom: 36px;
    height: 4px;
    background: var(--brand-blue-light);
  }

  .wordmark {
    position: absolute;
    display: flex; align-items: center; gap: 12px;
    color: var(--brand-blue);
    font-weight: 700;
    letter-spacing: 1px;
    line-height: 1;
  }
  .wordmark__square { display: block; background: var(--brand-blue); }

  .card--front .wordmark { left: 58px; top: 130px; font-size: 70px; }
  .card--front .wordmark__square { width: 26px; height: 26px; }
  .card--back .wordmark { left: 150px; top: 48px; font-size: 92px; }
  .card--back .wordmark__square { width: 32px; height: 32px; }

  .divider { position: absolute; width: 1px; background: var(--rule); }
  .card--front .divider { left: 300px; top: 56px; height: 220px; }
  .card--back .divider  { left: 312px; top: 160px; height: 120px; }

  .holder-name {
    color: var(--brand-blue);
    font-weight: 700;
    font-size: 21px;
    letter-spacing: .3px;
  }
  .address {
    color: var(--ink-soft);
    font-size: 15px;
    line-height: 1.3;
    margin-top: 14px;
  }

  .card--front .holder-name { position: absolute; left: 310px; top: 28px; }
  .card--front .address { position: absolute; left: 316px; top: 80px; margin: 0; }
  .card--back .identity { position: absolute; left: 56px; top: 178px; }
  .card--back .address { margin-top: 12px; }

  .contacts { position: absolute; list-style: none; }
  .card--front .contacts { left: 316px; top: 160px; }
  .card--back .contacts  { left: 330px; top: 160px; }
  .contacts li {
    display: flex; align-items: center; gap: 9px;
    color: var(--ink);
    font-size: 15px;
    height: 22px;
  }
  .contacts svg { width: 16px; height: 16px; flex: none; }
</style>
</head>
<body>
<main class="stage">

  <section class="card card--front" aria-label="TORV. business card, front">
    <div class="wordmark"><span class="wordmark__square"></span>TORV</div>
    <div class="divider"></div>
    <h1 class="holder-name">VIKRAM TULSE</h1>
    <p class="address">D-47, West Enclave-II ,<br>Nalvora 411902,<br>Devgiri, India</p>
    <ul class="contacts">
      <li><svg viewBox="0 0 16 16"><path d="M3 2c1-1 2 0 3 1.5S6.5 6 5.8 6.6c.8 1.7 2 2.9 3.6 3.6.6-.7 1.5-1.2 3-.2s2.5 2 1.5 3C12 15 9 14.5 5.5 11S1 5 3 2z" fill="var(--brand-blue)"/></svg>+91-124-5550182</li>
      <li><svg viewBox="0 0 16 16"><rect x="4.5" y="1" width="7" height="14" rx="1.5" fill="var(--brand-blue)"/><rect x="5.7" y="3" width="4.6" height="8" fill="#fff"/></svg>+91-9800555317</li>
      <li><svg viewBox="0 0 16 16"><rect x="2" y="6" width="12" height="8" rx="1.5" fill="var(--brand-blue)"/><rect x="4.5" y="2" width="7" height="5" fill="var(--brand-blue-light)"/></svg>+91-124-5550746</li>
      <li><svg viewBox="0 0 16 16"><circle cx="8" cy="8" r="7" fill="var(--brand-blue)"/><text x="8" y="11.5" text-anchor="middle" font-size="10" font-weight="700" fill="#fff" font-family="Arial, sans-serif">@</text></svg>vikram@torv.co.in</li>
      <li><svg viewBox="0 0 16 16"><circle cx="8" cy="8" r="7" fill="var(--brand-blue-light)"/><path d="M1 8h14M8 1c-3 3-3 11 0 14M8 1c3 3 3 11 0 14" stroke="#fff" stroke-width="1" fill="none"/></svg>www.torv.co.in</li>
    </ul>
    <div class="base-rule"></div>
    <div class="base-band"></div>
  </section>

  <section class="card card--back" aria-label="TORV. business card, back">
    <div class="wordmark"><span class="wordmark__square"></span>TORV</div>
    <div class="identity">
      <h2 class="holder-name">VIKRAM TULSE</h2>
      <p class="address">D-47, West Enclave-II ,<br>Nalvora 411902,<br>Devgiri, India</p>
    </div>
    <div class="divider"></div>
    <ul class="contacts">
      <li><svg viewBox="0 0 16 16"><path d="M3 2c1-1 2 0 3 1.5S6.5 6 5.8 6.6c.8 1.7 2 2.9 3.6 3.6.6-.7 1.5-1.2 3-.2s2.5 2 1.5 3C12 15 9 14.5 5.5 11S1 5 3 2z" fill="var(--brand-blue)"/></svg>+91-124-5550182</li>
      <li><svg viewBox="0 0 16 16"><rect x="4.5" y="1" width="7" height="14" rx="1.5" fill="var(--brand-blue)"/><rect x="5.7" y="3" width="4.6" height="8" fill="#fff"/></svg>+91-9800555317</li>
      <li><svg viewBox="0 0 16 16"><rect x="2" y="6" width="12" height="8" rx="1.5" fill="var(--brand-blue)"/><rect x="4.5" y="2" width="7" height="5" fill="var(--brand-blue-light)"/></svg>+91-124-5550746</li>
      <li><svg viewBox="0 0 16 16"><circle cx="8" cy="8" r="7" fill="var(--brand-blue)"/><text x="8" y="11.5" text-anchor="middle" font-size="10" font-weight="700" fill="#fff" font-family="Arial, sans-serif">@</text></svg>vikram@torv.co.in</li>
      <li><svg viewBox="0 0 16 16"><circle cx="8" cy="8" r="7" fill="var(--brand-blue-light)"/><path d="M1 8h14M8 1c-3 3-3 11 0 14M8 1c3 3 3 11 0 14" stroke="#fff" stroke-width="1" fill="none"/></svg>www.torv.co.in</li>
    </ul>
    <div class="base-rule"></div>
    <div class="base-band"></div>
  </section>

</main>
</body>
</html>
```